Website Design Request - Management Consulting Firm

We need a Website designed for an IT Management Staffing and Recruiting firm called TRAVENOK based in San Francisco.

The firm is an high-end technology staffing agency. Our focus is on quality and high-caliber candidates rather than quantity.

The website will have two main home pages. One for the recruiter and another on for the candidates.

The website needs to optimize for mobile devices as well.

I have attached few mock-ups that I have done just to show what I am thinking. The UI needs to be very clean, fluid, and it needs to have a modern, rustic, professional feel to it.

Target Market(s)

Technology Manager, Director, VP, CIO of Companies that have $4b-10b dollar revenue. Such as larkspurdwellings.example , https://www.velmorian.example/, quillnet.example, zib.example

Industry/Entity Type

Management Consulting

Number of Pages Required

5+ page

Font styles to use
Sans Serif

Colors
f37122
ffffff

Requirements
Must have
• Please review mock-ups for suggestions
Nice to have
Should not have

```html
<!DOCTYPE html>
<html lang="en">
<head>
<meta charset="utf-8">
<title>TRAVENOK — IT Project Management Jobs</title>
<link rel="stylesheet" href="https://fonts.googleapis.com/css2?family=Oswald:wght@400;500&family=Roboto:wght@400;500&family=Roboto+Condensed:wght@400&family=Open+Sans:wght@400&display=swap">
<style>
  :root {
    --orange: #f37122;
    --orange-soft: #f58a48;
    --orange-dark: #c9561a;
    --ink: #333333;
    --muted: #5b5b5b;
    --dark: #2e2e2e;
    --card-bg: #fafafa;
    --card-line: #e3e3e3;
    --white: #ffffff;
  }
  * { box-sizing: border-box; margin: 0; padding: 0; }
  html, body { width: 913px; height: 1200px; overflow: hidden; background: var(--white); }
  body { position: relative; font-family: 'Roboto', sans-serif; color: var(--ink); }
  .abs { position: absolute; }

  /* header */
  .site-header { position: absolute; left: 0; top: 0; width: 913px; height: 70px; background: var(--white); }
  .brand { left: 75px; top: 14px; font-family: 'Oswald', sans-serif; font-weight: 500; font-size: 30px; letter-spacing: 2px; color: var(--orange); line-height: 40px; }
  .nav-link { top: 29px; font-size: 10px; letter-spacing: .3px; color: var(--ink); text-transform: uppercase; line-height: 12px; }
  .btn-small { top: 23px; height: 24px; width: 61px; border-radius: 2px; color: var(--white); font-size: 9.5px; display: flex; align-items: center; justify-content: center; gap: 3px; text-transform: uppercase; }
  .btn-signin { left: 706px; background: var(--orange); box-shadow: 0 2px 0 var(--orange-dark); }
  .btn-signup { left: 776px; background: var(--dark); box-shadow: 0 2px 0 #111; }

  /* hero */
  .hero { left: 0; top: 70px; width: 913px; height: 424px; background: linear-gradient(110deg, #3a3f44 0%, #4a4e52 35%, #2f4a66 65%, #2b3440 100%); }
  .hero-title { left: 0; width: 913px; top: 184px; text-align: center; font-family: 'Oswald', sans-serif; font-weight: 400; font-size: 28px; color: var(--white); letter-spacing: -.3px; line-height: 36px; }
  .hero-sub { left: 0; width: 913px; top: 220px; text-align: center; font-family: 'Roboto Condensed', sans-serif; font-size: 16px; color: var(--white); line-height: 20px; }
  .email-field { left: 298px; top: 262px; width: 316px; height: 34px; background: var(--white); border-radius: 17px; font-family: 'Open Sans', sans-serif; font-size: 8.5px; color: #555; display: flex; align-items: center; justify-content: center; }
  .btn-offers { left: 378px; top: 310px; width: 157px; height: 30px; background: var(--orange); border-radius: 15px; box-shadow: 0 3px 0 var(--orange-dark); color: var(--white); font-size: 11.5px; display: flex; align-items: center; justify-content: center; }
  .hero-note { top: 366px; font-family: 'Open Sans', sans-serif; font-size: 9.5px; color: var(--white); line-height: 12px; }
  .hero-note.link { text-decoration: underline; }

  /* tabs */
  .tabs { left: 302px; top: 535px; }
  .tab-label { top: 545px; font-size: 15px; line-height: 20px; color: var(--white); }

  /* cards */
  .card { top: 621px; width: 180px; height: 247px; background: var(--card-bg); border: 1px solid var(--card-line); text-align: center; }
  .card-art { position: absolute; left: 55px; top: 20px; width: 68px; height: 98px; border-radius: 6px; background: linear-gradient(180deg, var(--orange-soft), var(--orange)); }
  .card-title { position: absolute; left: 0; width: 100%; top: 130px; font-size: 15.5px; font-weight: 400; color: var(--ink); line-height: 20px; }
  .card-text { position: absolute; left: 14px; right: 14px; top: 155px; font-family: 'Open Sans', sans-serif; font-size: 8.6px; line-height: 15.6px; color: var(--muted); }

  .btn-upload { left: 368px; top: 913px; width: 177px; height: 30px; background: var(--orange); border-radius: 15px; box-shadow: 0 3px 0 var(--orange-dark); color: var(--white); font-size: 12px; display: flex; align-items: center; justify-content: center; gap: 4px; text-transform: uppercase; }

  /* subscribe */
  .subscribe { left: 0; top: 998px; width: 913px; height: 76px; background: linear-gradient(100deg, #2b2b2b, #1f1f1f 60%, #2a2a2a); }
  .subscribe-text { left: 185px; top: 1021px; font-size: 12px; line-height: 17.5px; color: var(--white); text-transform: uppercase; }
  .subscribe-field { left: 425px; top: 1022px; width: 290px; height: 32px; background: var(--white); border-radius: 16px 0 0 16px; font-family: 'Open Sans', sans-serif; font-size: 9px; color: #555; display: flex; align-items: center; padding-left: 19px; }
  .btn-subscribe { left: 709px; top: 1022px; width: 96px; height: 32px; background: var(--orange); border-radius: 0 16px 16px 0; color: var(--white); font-size: 10px; display: flex; align-items: center; justify-content: center; text-transform: uppercase; }

  /* footer */
  .social { top: 1104px; width: 20px; height: 20px; border-radius: 50%; background: #6f6f6f; }
  .footer-links { left: 0; width: 913px; top: 1140px; text-align: center; font-size: 8.8px; color: var(--ink); text-transform: uppercase; line-height: 12px; }
  .footer-links span.sep { margin: 0 6px; }
  .copyright { left: 0; width: 913px; top: 1160px; text-align: center; font-family: 'Open Sans', sans-serif; font-size: 9.2px; color: var(--ink); line-height: 12px; }
</style>
</head>
<body>

<header class="site-header">
  <div class="abs brand">TRAVENOK</div>
  <nav>
    <span class="abs nav-link" style="left:469px">Home</span>
    <span class="abs nav-link" style="left:525px">Professionals</span>
    <span class="abs nav-link" style="left:631px">Employers</span>
    <span class="abs btn-small btn-signin">
      <svg width="8" height="8" viewBox="0 0 8 8"><circle cx="4" cy="2.2" r="2" fill="#fff"/><path d="M0.5 8 C0.5 5 7.5 5 7.5 8Z" fill="#fff"/></svg>Sign In</span>
    <span class="abs btn-small btn-signup">
      <svg width="7" height="9" viewBox="0 0 7 9"><path d="M1.5 4 V2.5 a2 2 0 0 1 4 0" stroke="#fff" stroke-width="1.2" fill="none"/><rect x="0" y="4" width="7" height="5" rx="1" fill="#fff"/></svg>Sign Up</span>
  </nav>
</header>

<section>
  <div class="abs hero" role="img" aria-label="Photo of a team of IT professionals working together at laptops in a bright office"></div>
  <h1 class="abs hero-title">LOOKING FOR IT PROJECT MANAGEMENT JOBS?</h1>
  <p class="abs hero-sub">Upload your resume, accept interview requests, get offers</p>
  <div class="abs email-field">Your Email Address</div>
  <div class="abs btn-offers">GET OFFERS NOW</div>
  <span class="abs hero-note" style="left:330px">Looking for talents?</span>
  <span class="abs hero-note link" style="left:445px">See how it works for employers</span>
</section>

<section>
  <svg class="abs tabs" width="310" height="40" viewBox="0 0 310 40">
    <path d="M10 0 H165 L185 20 L165 40 H10 L0 20 Z" fill="#2e2e2e"/>
    <path d="M162 0 H290 L310 20 L290 40 H162 L182 20 Z" fill="#f37122"/>
  </svg>
  <span class="abs tab-label" style="left:334px">HOW IT WORKS?</span>
  <span class="abs tab-label" style="left:506px">WHY US?</span>

  <article class="abs card" style="left:75px">
    <div class="card-art" role="img" aria-label="Illustration of a head-shaped lightbulb with a dollar sign"></div>
    <h2 class="card-title">Get Paid More</h2>
    <p class="card-text">On average, TRAVENOK candidates get upto 20% more for their skills. Our Talent engines makes you discoverable for your niche project experience</p>
  </article>

  <article class="abs card" style="left:270px">
    <div class="card-art" role="img" aria-label="Illustration of a head-shaped lightbulb with a phone handset"></div>
    <h2 class="card-title">Less Interviews</h2>
    <p class="card-text">Experince fewer interviews with TRAVENOK to get the right job. Our platform matches you against your specilized project experinces, industry exposure and core PM skills</p>
  </article>

  <article class="abs card" style="left:464px">
    <div class="card-art" role="img" aria-label="Illustration of a head-shaped lightbulb with a magnifying glass"></div>
    <h2 class="card-title">Transperency</h2>
    <p class="card-text">In order to promote win-win scenarios for our clients and consultants, we provide 100% transparency in all our services</p>
  </article>

  <article class="abs card" style="left:658px">
    <div class="card-art" role="img" aria-label="Illustration of a head-shaped lightbulb with a thumbs-up hand"></div>
    <h2 class="card-title">Make better decisions</h2>
    <p class="card-text">Employers who have considered all their options and carefully made a decision to join us understand that we bring the highest caliber candidates for the jobs</p>
  </article>

  <div class="abs btn-upload">
    <svg width="11" height="11" viewBox="0 0 11 11"><path d="M5.5 0 L10 4.5 H7 V8 H4 V4.5 H1Z" fill="#fff"/><rect x="0" y="9" width="11" height="2" fill="#fff"/></svg>Upload your resume</div>
</section>

<section>
  <div class="abs subscribe"></div>
  <svg class="abs" style="left:52px;top:1000px" width="78" height="72" viewBox="0 0 78 72">
    <g transform="rotate(-35 39 36)" stroke="#5a5a5a" stroke-width="3" fill="none">
      <rect x="10" y="18" width="58" height="38" rx="3"/>
      <path d="M10 20 L39 42 L68 20"/>
    </g>
  </svg>
  <svg class="abs" style="left:143px;top:1024px" width="30" height="28" viewBox="0 0 30 28">
    <path d="M28 2 L2 13 L11 16 L13 26 L17 19 L24 23 Z M11 16 L28 2 M13 26 L15 17" stroke="#fff" stroke-width="2" fill="none" stroke-linejoin="round"/>
  </svg>
  <p class="abs subscribe-text">Subscribe to receive updates and<br>exclusive offers.</p>
  <div class="abs subscribe-field">Enter your E - mail</div>
  <div class="abs btn-subscribe">Subscribe</div>
</section>

<footer>
  <span class="abs social" style="left:391px"></span>
  <span class="abs social" style="left:419px"></span>
  <span class="abs social" style="left:446px"></span>
  <span class="abs social" style="left:474px"></span>
  <span class="abs social" style="left:501px"></span>
  <p class="abs footer-links">Home<span class="sep">/</span>Professionals<span class="sep">/</span>Employers<span class="sep">/</span>Sign In<span class="sep">/</span>Sign Up<span class="sep">/</span>Contact Us</p>
  <p class="abs copyright">2016 © Copyrights Travenok.All Rights Reserved</p>
</footer>

</body>
</html>
```